Small legal and financial translation company needs Squarespace website, brochure and logo

Hello,
We are Lumarin Services (www.lumarinservices-example.com), a boutique legal and financial translation company. We offer our services mainly to Spanish customers. Our primary line of business is the translation of financial statements, but we translate a wide variety legal and financial texts.
The project we are offering comprises three parts: a redo of the current website, an informational brochure for potential customer and a logo design. These three parts should provide a consistent image. We would develop content soon.
We are looking for a website that would look like a typical law firm website, nothing too fancy. Right now, it is in English, Spanish and French, although the new site need only be in English and Spanish. There must be good toggling between the English and Spanish versions. There would be no need for tie-ins to social media and it would not contain a blog. Basically, a static site. We aren't interesting in driving traffic to the site or SEO, as we will contact nearly all potential customers beforehand. The website must be built in Squarespace to enable a smooth transition. The content would be similar to the current page, we'll be working on the exact content, but a rough draft is attached.
The brochure will be some three pages and would introduce the company to potential customers, using similar images as the website and the logo to be designed.
The only specifications for the logo is, as the website and brochure, it convey a sense of security and trust.
Feel free to ask with any questions as this is the first time we have used this platform.
Thank you!
Updates

I've added a more or less final version for the text in the brochure and updated the brief. Added Wednesday, June 10, 2015

Target Market(s)

Spanish law firms, auditors, accountants, banks, investment firms

Industry/Entity Type

Finance

Logo Text

Lumarin Services

Number of Pages Required

5+ page

Font styles to use
Serif

Requirements
Must have
• The website must be built in Squarespace and have a good option to toggle between English and Spanish versions.
• Brochure must be in both English and Spanish, I'm attaching a rough draft of the information that it will probably have. This should give an idea about what to include and the spacing. I will update it to include the final information.
Nice to have
• Would be nice to have some quality finance- and legal-related images
Should not have
• Vibrant colours

```html
<!DOCTYPE html>
<html lang="en">
<head>
<meta charset="utf-8">
<title>Lumarin Services Brochure</title>
<link rel="stylesheet" href="https://fonts.googleapis.com/css2?family=EB+Garamond:ital,wght@0,400;0,500;0,700;1,400&family=Open+Sans:wght@400;600&display=swap">
<style>
:root{
  --crimson:#7b0f1a;
  --crimson-dark:#5e0a13;
  --ink:#0c0c0c;
  --paper:#ffffff;
  --stage:#e9e9e9;
  --label:#4a4a4a;
  --body:#3a3a3a;
  --muted:#cfcfcf;
  --table-a:#d7d7d7;
  --table-b:#e1e1e1;
  --panel-a:#e4e4e4;
  --panel-b:#ededed;
}
*{margin:0;padding:0;box-sizing:border-box}
html,body{width:1200px;height:1063px;overflow:hidden}
body{background:var(--stage);position:relative;font-family:"EB Garamond",Georgia,serif;color:var(--body)}
.spread-label{position:absolute;font-family:"Open Sans",Arial,sans-serif;font-size:14px;color:var(--label);transform:translateX(-50%);white-space:nowrap}
.spread{position:absolute;width:548px;height:423px;box-shadow:0 3px 8px rgba(0,0,0,.35);overflow:hidden;background:var(--paper)}
.spread > svg.shapes{position:absolute;left:0;top:0}
.page{position:absolute;top:0;width:274px;height:423px}
.page.left{left:0}.page.right{left:274px}
.abs{position:absolute}
.heading{font-variant:small-caps;color:var(--crimson);font-size:14px;letter-spacing:.6px;font-weight:400}
.heading.light{color:var(--paper)}
.copy{font-size:6.3px;line-height:1.3;text-align:justify;color:var(--body)}
.copy.light{color:#d6d6d6}
.site{position:absolute;left:12px;top:402px;font-size:10px;color:var(--paper)}

/* cover spread */
.back-intro{left:20px;top:41px;width:242px;font-size:7.6px;line-height:1.38;color:#e2e2e2}
.contact-title{left:13px;top:283px;font-size:12.5px;font-weight:700;color:var(--paper)}
.contact-line{left:15px;font-size:7.2px;color:#eee}
.wordmark{left:44px;top:20px;display:flex;align-items:center;gap:6px}
.wordmark .mark{width:18px;height:18px;background:var(--crimson)}
.wordmark .name{font-size:21px;letter-spacing:.8px;color:var(--ink)}
.cover-tagline{left:0;width:274px;top:316px;text-align:center;font-size:16.5px;line-height:1.36;color:var(--paper)}
.cover-site{left:0;width:274px;top:397px;text-align:center;font-size:10px;color:#eee}

/* page 1 */
.stat-number{font-size:23px;color:var(--ink);width:70px;text-align:center}
.stat-label{font-size:5.8px;color:#555;width:90px;text-align:center}

/* page 2 */
.reason-icon{position:absolute;left:22px;width:19px;height:19px;border-radius:50%;background:var(--paper)}
.reason-title{position:absolute;left:52px;font-size:8.6px;color:var(--paper)}
.reason-copy{position:absolute;left:52px;width:210px}

/* page 3 */
.expertise-num{position:absolute;left:13px;width:29px;height:29px;border:1px solid var(--ink);border-radius:50%;font-size:15px;text-align:center;line-height:27px;color:var(--ink)}
.expertise-title{position:absolute;left:47px;font-size:7.5px;font-weight:700;color:var(--ink)}
.expertise-copy{position:absolute;left:47px;width:215px}

/* page 4 */
.compare-title{left:0;width:274px;top:16px;text-align:center;color:var(--paper);font-size:12px;letter-spacing:1.4px;line-height:1.16;font-variant:small-caps}
.compare-col{position:absolute;top:78px;width:124px}
.compare-head{height:29px;background:var(--crimson);color:var(--paper);font-size:10px;line-height:29px;text-align:center}
.compare-body{height:236px;padding:7px 6px}
.compare-body .copy{margin-bottom:22px}

/* page 5 */
.price-table{position:absolute;left:10px;top:47px;width:253px;border-collapse:collapse;background:var(--table-b)}
.price-table th{height:16px;font-size:6px;font-weight:700;color:#333;text-align:center;background:var(--table-b)}
.price-table th.item{background:var(--table-a)}
.price-table td{height:31.3px;font-size:9px;color:#444;text-align:center;border-top:1px solid #f4f4f4}
.price-table td.item{background:var(--table-a);font-size:5.6px;line-height:1.2;text-align:left;padding-left:9px;width:105px;color:#555}

/* page 6 */
.client{position:absolute;left:0;width:274px;height:100px}
.client-photo{position:absolute;left:12px;top:2px;width:58px;height:58px;border-radius:50%;background:radial-gradient(circle at 50% 40%,#c8a78f,#6f5a4c)}
.client-name{position:absolute;left:8px;top:70px;width:66px;text-align:center;font-family:"Open Sans",Arial,sans-serif;font-size:6.5px;color:#222}
.client-quote{position:absolute;left:88px;top:4px;width:172px;font-size:6.3px;line-height:1.42;font-style:italic;text-align:justify;color:#333}
.qmark{position:absolute;font-size:20px;font-weight:700;color:var(--ink);line-height:1}
.client-rule{position:absolute;left:88px;width:172px;height:1px;background:#cfcfcf}
</style>
</head>
<body>

<div class="spread-label" style="left:165px;top:33px">Back</div>
<div class="spread-label" style="left:440px;top:33px">Cover</div>
<div class="spread-label" style="left:752px;top:33px">Page 1</div>
<div class="spread-label" style="left:1030px;top:33px">Page 2</div>
<div class="spread-label" style="left:171px;top:546px">Page 3</div>
<div class="spread-label" style="left:443px;top:546px">Page 4</div>
<div class="spread-label" style="left:758px;top:546px">Page 5</div>
<div class="spread-label" style="left:1030px;top:546px">Page 6</div>

<!-- Back + Cover -->
<section class="spread" style="left:30px;top:63px">
  <svg class="shapes" width="548" height="423" viewBox="0 0 548 423">
    <defs>
      <linearGradient id="towerShade" x1="0" y1="0" x2="1" y2="1">
        <stop offset="0" stop-color="#2c2c2c"/><stop offset="1" stop-color="#0b0b0b"/>
      </linearGradient>
      <linearGradient id="deskShade" x1="0" y1="0" x2="1" y2="1">
        <stop offset="0" stop-color="#f2f2f2"/><stop offset=".55" stop-color="#bdbdbd"/><stop offset="1" stop-color="#6d6d6d"/>
      </linearGradient>
    </defs>
    <rect x="0" y="0" width="274" height="423" fill="var(--ink)"/>
    <polygon points="0,0 274,0 274,292 0,210" fill="url(#towerShade)" role="img" aria-label="Photo of an office tower in black and white"/>
    <polygon points="0,210 274,294 274,318 0,423" fill="var(--crimson)"/>
    <rect x="274" y="0" width="274" height="423" fill="var(--paper)"/>
    <rect x="274" y="75" width="274" height="245" fill="url(#deskShade)" role="img" aria-label="Photo of a hand signing a document beside a scales-of-justice statue"/>
    <polygon points="274,318 548,290 548,423 274,423" fill="var(--ink)"/>
    <polygon points="490,238 548,238 548,292" fill="var(--crimson)"/>
  </svg>
  <div class="page left">
    <p class="abs back-intro">Throughout our careers, we have observed a marked deficiency in translations with respect to quality and price. A high-value translation at a reasonable price does seem to be readily available and so we look to offer translations that respect your company's image as much as its pocketbook. In short, a high added-value product of impeccable quality at prices in line with today's dynamics.</p>
    <h3 class="abs contact-title">Contact Us</h3>
    <p class="abs contact-line" style="top:308px">18 Harbor Lane Westbrook, FL 30000</p>
    <p class="abs contact-line" style="top:323px">(555) 764-0100</p>
    <p class="abs contact-line" style="top:339px">info@lumarinservices-example.com</p>
    <p class="abs contact-line" style="top:355px">www.lumarinservices-example.com</p>
  </div>
  <div class="page right">
    <div class="abs wordmark"><span class="mark"></span><span class="name">LUMARIN SERVICES</span></div>
    <p class="abs cover-tagline">High-quality translation services<br>in &nbsp;English, Spanish and French<br>for legal and financial documents</p>
    <p class="abs cover-site">www.lumarinservices-example.com</p>
  </div>
</section>

<!-- Page 1 + Page 2 -->
<section class="spread" style="left:617px;top:63px">
  <svg class="shapes" width="548" height="423" viewBox="0 0 548 423">
    <defs>
      <linearGradient id="teamShade" x1="0" y1="0" x2="1" y2="1">
        <stop offset="0" stop-color="#d8d8d8"/><stop offset="1" stop-color="#4a4a4a"/>
      </linearGradient>
    </defs>
    <rect x="274" y="0" width="274" height="423" fill="var(--ink)"/>
    <rect x="13" y="42" width="118" height="104" fill="url(#teamShade)" role="img" aria-label="Photo of a team of business professionals"/>
    <circle cx="49" cy="289" r="33" fill="none" stroke="var(--crimson)" stroke-width="1.4"/>
    <circle cx="134" cy="289" r="33" fill="none" stroke="var(--crimson)" stroke-width="1.4"/>
    <circle cx="220" cy="289" r="33" fill="none" stroke="var(--crimson)" stroke-width="1.4"/>
    <polygon points="0,373 274,400 274,423 0,423" fill="var(--crimson)"/>
    <polygon points="150,423 274,380 274,423" fill="var(--ink)"/>
    <polygon points="274,373 548,400 548,423 274,423" fill="var(--crimson)"/>
    <polygon points="424,423 548,380 548,423" fill="#000"/>
  </svg>
  <div class="page left">
    <h2 class="abs heading" style="left:12px;top:15px">Who Are We?</h2>
    <p class="abs copy" style="left:140px;top:41px;width:116px;font-size:6.4px;line-height:1.42">We are a small, highly professional and qualified group of professionals with backgrounds in law, financial services and translation and interpretation that boasts experience in global consulting and auditing firms, law firms and companies from a cross section of industries. Sensitive to the workings of the financial world, we are detail-oriented experts striving to facilitate understanding among investors, companies and international organisations.</p>
    <h2 class="abs heading" style="left:14px;top:164px">Experience You Can Trust On</h2>
    <p class="abs copy" style="left:14px;top:186px;width:248px">Lorem ipsum dolor sit amet, consectetuer adipiscing elit, sed diam nonummy nibh euismod tincidunt ut laoreet dolore magna aliquam erat volutpat. Ut wisi enim ad minim veniam, quis nostrud exerci tation ullamcorper suscipit lobortis nisl ut aliquip ex ea commodo consequat. Duis autem vel eum iriure dolor in hendrerit in vulputate velit esse molestie consequat, vel illum dolore eu feugiat nulla facilisis at vero eros et accumsan et iusto odio.</p>
    <p class="abs stat-number" style="left:14px;top:273px">4589</p>
    <p class="abs stat-number" style="left:99px;top:273px">152</p>
    <p class="abs stat-number" style="left:185px;top:273px">64</p>
    <p class="abs stat-label" style="left:4px;top:329px">Nos of Words Translated</p>
    <p class="abs stat-label" style="left:89px;top:329px">Nos of Documents Translated</p>
    <p class="abs stat-label" style="left:175px;top:329px">Nos of Satisfied Clients</p>
    <p class="site">www.lumarinservices-example.com</p>
  </div>
  <div class="page right">
    <h2 class="abs heading light" style="left:20px;top:16px">Why Choose Lumarin?</h2>

    <span class="reason-icon" style="top:44px"></span>
    <p class="reason-title" style="top:44px">Save Money</p>
    <p class="reason-copy copy light" style="top:58px">Lorem ipsum dolor sit amet, consectetuer adipiscing elit, sed diam nonummy nibh euismod tincidunt ut laoreet dolore magna aliquam erat volutpat. Ut wisi enim ad minim veniam, quis nostrud exerci tation ullamcorper suscipit lobortis nisl ut aliquip ex ea commodo consequat.</p>

    <span class="reason-icon" style="top:110px"></span>
    <p class="reason-title" style="top:110px">Quality Guaranteed</p>
    <p class="reason-copy copy light" style="top:124px">Lorem ipsum dolor sit amet, consectetuer adipiscing elit, sed diam nonummy nibh euismod tincidunt ut laoreet dolore magna aliquam erat volutpat. Ut wisi enim ad minim veniam, quis nostrud exerci tation ullamcorper suscipit lobortis nisl ut aliquip ex ea commodo consequat.</p>

    <span class="reason-icon" style="top:176px"></span>
    <p class="reason-title" style="top:176px">Native Translators Only</p>
    <p class="reason-copy copy light" style="top:190px">Lorem ipsum dolor sit amet, consectetuer adipiscing elit, sed diam nonummy nibh euismod tincidunt ut laoreet dolore magna aliquam erat volutpat. Ut wisi enim ad minim veniam, quis nostrud exerci tation ullamcorper suscipit lobortis nisl ut aliquip ex ea commodo consequat.</p>

    <span class="reason-icon" style="top:242px"></span>
    <p class="reason-title" style="top:242px">Consistency Over Time</p>
    <p class="reason-copy copy light" style="top:256px">Lorem ipsum dolor sit amet, consectetuer adipiscing elit, sed diam nonummy nibh euismod tincidunt ut laoreet dolore magna aliquam erat volutpat. Ut wisi enim ad minim veniam, quis nostrud exerci tation ullamcorper suscipit lobortis nisl ut aliquip ex ea commodo consequat.</p>

    <span class="reason-icon" style="top:308px"></span>
    <p class="reason-title" style="top:308px">Use of Technology Helps Cut Costs</p>
    <p class="reason-copy copy light" style="top:322px">Lorem ipsum dolor sit amet, consectetuer adipiscing elit, sed diam nonummy nibh euismod tincidunt ut laoreet dolore magna aliquam erat volutpat. Ut wisi enim ad minim veniam, quis nostrud exerci tation ullamcorper suscipit lobortis nisl ut aliquip ex ea commodo consequat.</p>

    <p class="site">www.lumarinservices-example.com</p>
  </div>
</section>

<!-- Page 3 + Page 4 -->
<section class="spread" style="left:30px;top:576px">
  <svg class="shapes" width="548" height="423" viewBox="0 0 548 423">
    <defs>
      <linearGradient id="penShade" x1="0" y1="0" x2="1" y2="1">
        <stop offset="0" stop-color="#9a9a9a"/><stop offset=".5" stop-color="#d6d6d6"/><stop offset="1" stop-color="#f4f4f4"/>
      </linearGradient>
    </defs>
    <rect x="0" y="0" width="274" height="145" fill="url(#penShade)" role="img" aria-label="Photo of a hand writing with a pen on papers"/>
    <rect x="274" y="0" width="274" height="423" fill="var(--ink)"/>
    <rect x="285" y="107" width="124" height="236" fill="var(--panel-a)"/>
    <rect x="414" y="107" width="124" height="236" fill="var(--panel-b)"/>
    <polygon points="0,373 274,400 274,423 0,423" fill="var(--crimson)"/>
    <polygon points="150,423 274,380 274,423" fill="var(--ink)"/>
    <polygon points="274,373 548,400 548,423 274,423" fill="var(--crimson)"/>
    <polygon points="424,423 548,380 548,423" fill="#000"/>
  </svg>
  <div class="page left">
    <h2 class="abs heading" style="left:13px;top:141px">Areas of Expertise</h2>

    <span class="expertise-num" style="top:170px">1</span>
    <p class="expertise-title" style="top:170px">Duis autem vel eum iriure dolor</p>
    <p class="expertise-copy copy" style="top:182px">Lorem ipsum dolor sit amet, consectetuer adipiscing elit, sed diam nonummy nibh euismod tincidunt ut laoreet dolore magna aliquam erat volutpat. Ut wisi enim ad minim veniam, quis nostrud exerci tation ullamcorper suscipit lobortis nisl ut aliquip ex ea commodo consequat.</p>

    <span class="expertise-num" style="top:237px">2</span>
    <p class="expertise-title" style="top:238px">Duis autem vel eum iriure dolor</p>
    <p class="expertise-copy copy" style="top:250px">Lorem ipsum dolor sit amet, consectetuer adipiscing elit, sed diam nonummy nibh euismod tincidunt ut laoreet dolore magna aliquam erat volutpat. Ut wisi enim ad minim veniam, quis nostrud exerci tation ullamcorper suscipit lobortis nisl ut aliquip ex ea commodo consequat.</p>

    <span class="expertise-num" style="top:301px">3</span>
    <p class="expertise-title" style="top:302px">Duis autem vel eum iriure dolor</p>
    <p class="expertise-copy copy" style="top:314px">Lorem ipsum dolor sit amet, consectetuer adipiscing elit, sed diam nonummy nibh euismod tincidunt ut laoreet dolore magna aliquam erat volutpat. Ut wisi enim ad minim veniam, quis nostrud exerci tation ullamcorper suscipit lobortis nisl ut aliquip ex ea commodo consequat.</p>

    <p class="site">www.lumarinservices-example.com</p>
  </div>
  <div class="page right">
    <h2 class="abs compare-title">Differences between working<br>with a translation agency<br>and a translation provider</h2>
    <div class="compare-col" style="left:11px">
      <div class="compare-head">Translation Agency</div>
      <div class="compare-body">
        <p class="copy">Lorem ipsum dolor sit amet, consectetuer adipiscing elit, sed diam nonummy nibh euismod tincidunt ut laoreet dolore magna aliquam erat volutpat. Ut wisi enim ad minim veniam, quis nostrud exerci tation ullamcorper suscipit lobortis nisl ut aliquip ex ea commodo consequat.</p>
        <p class="copy">Lorem ipsum dolor sit amet, consectetuer adipiscing elit, sed diam nonummy nibh euismod tincidunt ut laoreet dolore magna aliquam erat volutpat. Ut wisi enim ad minim veniam, quis nostrud exerci tation ullamcorper suscipit lobortis nisl ut aliquip ex ea commodo consequat.</p>
        <p class="copy">Lorem ipsum dolor sit amet, consectetuer adipiscing elit, sed diam nonummy nibh euismod tincidunt ut laoreet dolore magna aliquam erat volutpat. Ut wisi enim ad minim veniam, quis nostrud exerci tation ullamcorper suscipit lobortis nisl ut aliquip ex ea commodo consequat.</p>
      </div>
    </div>
    <div class="compare-col" style="left:140px">
      <div class="compare-head">Translation Provider</div>
      <div class="compare-body">
        <p class="copy">Lorem ipsum dolor sit amet, consectetuer adipiscing elit, sed diam nonummy nibh euismod tincidunt ut laoreet dolore magna aliquam erat volutpat. Ut wisi enim ad minim veniam, quis nostrud exerci tation ullamcorper suscipit lobortis nisl ut aliquip ex ea commodo consequat.</p>
        <p class="copy">Lorem ipsum dolor sit amet, consectetuer adipiscing elit, sed diam nonummy nibh euismod tincidunt ut laoreet dolore magna aliquam erat volutpat. Ut wisi enim ad minim veniam, quis nostrud exerci tation ullamcorper suscipit lobortis nisl ut aliquip ex ea commodo consequat.</p>
        <p class="copy">Lorem ipsum dolor sit amet, consectetuer adipiscing elit, sed diam nonummy nibh euismod tincidunt ut laoreet dolore magna aliquam erat volutpat. Ut wisi enim ad minim veniam, quis nostrud exerci tation ullamcorper suscipit lobortis nisl ut aliquip ex ea commodo consequat.</p>
      </div>
    </div>
    <p class="site">www.lumarinservices-example.com</p>
  </div>
</section>

<!-- Page 5 + Page 6 -->
<section class="spread" style="left:617px;top:576px">
  <svg class="shapes" width="548" height="423" viewBox="0 0 548 423">
    <polygon points="0,373 274,400 274,423 0,423" fill="var(--crimson)"/>
    <polygon points="150,423 274,380 274,423" fill="var(--ink)"/>
    <polygon points="274,373 548,400 548,423 274,423" fill="var(--crimson)"/>
    <polygon points="424,423 548,380 548,423" fill="var(--ink)"/>
  </svg>
  <div class="page left">
    <h2 class="abs heading" style="left:10px;top:16px">Translation Pricing</h2>
    <table class="price-table">
      <thead><tr><th class="item"></th><th>Standard</th><th>Advance</th></tr></thead>
      <tbody>
        <tr><td class="item">Lorem ipsum dolor sit amet,<br>consectetuer adipiscing elit</td><td>$100</td><td>$200</td></tr>
        <tr><td class="item">Lorem ipsum dolor sit amet,<br>consectetuer adipiscing elit</td><td>$100</td><td>$200</td></tr>
        <tr><td class="item">Lorem ipsum dolor sit amet,<br>consectetuer adipiscing elit</td><td>$100</td><td>$200</td></tr>
        <tr><td class="item">Lorem ipsum dolor sit amet,<br>consectetuer adipiscing elit</td><td>$100</td><td>$200</td></tr>
        <tr><td class="item">Lorem ipsum dolor sit amet,<br>consectetuer adipiscing elit</td><td>$100</td><td>$200</td></tr>
        <tr><td class="item">Lorem ipsum dolor sit amet,<br>consectetuer adipiscing elit</td><td>$100</td><td>$200</td></tr>
        <tr><td class="item">Lorem ipsum dolor sit amet,<br>consectetuer adipiscing elit</td><td>$100</td><td>$200</td></tr>
        <tr><td class="item">Lorem ipsum dolor sit amet,<br>consectetuer adipiscing elit</td><td>$100</td><td>$200</td></tr>
        <tr><td class="item">Lorem ipsum dolor sit amet,<br>consectetuer adipiscing elit</td><td>$100</td><td>$200</td></tr>
      </tbody>
    </table>
    <p class="site">www.lumarinservices-example.com</p>
  </div>
  <div class="page right">
    <h2 class="abs heading" style="left:14px;top:16px">Our Clients</h2>
    <p class="abs copy" style="left:16px;top:46px;width:246px;text-align:left">Lorem ipsum dolor sit amet, consectetuer adipiscing elit, sed diam nonummy nibh euismod tincidunt ut laoreet dolore magna aliquam erat volutpat</p>

    <div class="client" style="top:77px">
      <div class="client-photo" role="img" aria-label="Portrait photo of client"></div>
      <p class="client-name">Mr. Daniel Hart</p>
      <span class="qmark" style="left:76px;top:0">&ldquo;</span>
      <p class="client-quote">Lorem ipsum dolor sit amet, consectetuer adipiscing elit, sed diam nonummy nibh euismod tincidunt ut laoreet dolore magna aliquam erat volutpat. Ut wisi enim ad minim veniam, quis nostrud exerci tation ullamcorper suscipit lobortis nisl ut aliquip ex ea commodo consequat. Duis autem vel eum iriure dolor in hendrerit in vulputate velit esse molestie consequat, vel illum</p>
      <span class="qmark" style="left:220px;top:62px">&rdquo;</span>
    </div>
    <span class="client-rule" style="top:171px"></span>

    <div class="client" style="top:182px">
      <div class="client-photo" role="img" aria-label="Portrait photo of client"></div>
      <p class="client-name">Mr. Daniel Hart</p>
      <span class="qmark" style="left:76px;top:0">&ldquo;</span>
      <p class="client-quote">Lorem ipsum dolor sit amet, consectetuer adipiscing elit, sed diam nonummy nibh euismod tincidunt ut laoreet dolore magna aliquam erat volutpat. Ut wisi enim ad minim veniam, quis nostrud exerci tation ullamcorper suscipit lobortis nisl ut aliquip ex ea commodo consequat. Duis autem vel eum iriure dolor in hendrerit in vulputate velit esse molestie consequat, vel illum</p>
      <span class="qmark" style="left:220px;top:62px">&rdquo;</span>
    </div>
    <span class="client-rule" style="top:276px"></span>

    <div class="client" style="top:287px">
      <div class="client-photo" role="img" aria-label="Portrait photo of client"></div>
      <p class="client-name">Mr. Daniel Hart</p>
      <span class="qmark" style="left:76px;top:0">&ldquo;</span>
      <p class="client-quote">Lorem ipsum dolor sit amet, consectetuer adipiscing elit, sed diam nonummy nibh euismod tincidunt ut laoreet dolore magna aliquam erat volutpat. Ut wisi enim ad minim veniam, quis nostrud exerci tation ullamcorper suscipit lobortis nisl ut aliquip ex ea commodo consequat. Duis autem vel eum iriure dolor in hendrerit in vulputate velit esse molestie consequat, vel illum</p>
      <span class="qmark" style="left:220px;top:62px">&rdquo;</span>
    </div>

    <p class="site">www.lumarinservices-example.com</p>
  </div>
</section>

</body>
</html>
```